Thornbury Building Company - Card Design

I am looking to use the logo designs that you already did for me to develop a business card. I would like the card to have a black background and be double sided. I want white and green logo and text. I have attached an inspiration photo of a look that I like. I would like to use the Vertical Logo attached to take up the full front side of the card. On the back where I have my name and information, I would like to have the horizontal logo or maybe even just the image of the 'A' and trees without the text. I am open, but I am looking for something clean and simple and I want the green to really pop! Additional files can be found under Design #: 58302946

Target Market(s)

Homeowners

Industry/Entity Type

Construction

Contact Information for Business Card

Name: Marcus Thornbury, Title: Project Manager, Phone: 555.274.8136, Email: thornburybuildingcompany@mailvesta.com, address: 487 Larkspur Ln, Wrenfield, CA 95033, Lic# 2468317

Colors
00AB8E
00BBA5
67D7C9
C6EFE9
E9F9F6

Requirements
Nice to have
• I would like to see the logos that I have already got from ArtLoomHub, though I am open to new ones

```html
<!DOCTYPE html>
<html lang="en">
<head>
<meta charset="utf-8">
<title>Thornbury Building Company – Business Card</title>
<link rel="stylesheet" href="https://fonts.googleapis.com/css2?family=Montserrat:wght@400;500;700;800&display=swap">
<style>
  :root {
    --bg: #242424;
    --card: #1c1c1c;
    --green: #6cb944;
    --white: #ffffff;
  }
  html, body {
    margin: 0;
    padding: 0;
    width: 1200px;
    height: 988px;
    overflow: hidden;
    background: var(--bg);
    font-family: "Montserrat", sans-serif;
  }
  .canvas {
    position: relative;
    width: 1200px;
    height: 988px;
  }
  .card {
    position: absolute;
    width: 700px;
    height: 400px;
    background: var(--card);
    border-radius: 22px;
    box-shadow: 0 18px 40px rgba(0,0,0,0.55);
    overflow: hidden;
  }
  .card--front { left: 70px; top: 60px; }
  .card--back { left: 430px; top: 528px; }

  /* Front: brand name */
  .brand {
    position: absolute;
    inset: 0;
    display: flex;
    align-items: center;
    justify-content: center;
    gap: 18px;
  }
  .brand__square {
    width: 40px;
    height: 40px;
    background: var(--green);
    flex: none;
  }
  .brand__name {
    margin: 0;
    color: var(--white);
    font-weight: 800;
    font-size: 30px;
    letter-spacing: 1px;
    text-transform: uppercase;
    line-height: 1.15;
  }

  /* Back */
  .back-brand {
    position: absolute;
    right: 44px;
    top: 44px;
    display: flex;
    align-items: center;
    gap: 12px;
  }
  .back-brand .brand__square { width: 26px; height: 26px; }
  .back-brand__name {
    margin: 0;
    color: var(--green);
    font-weight: 800;
    font-size: 20px;
    text-transform: uppercase;
    letter-spacing: 1px;
    text-align: right;
    line-height: 1.2;
  }
  .divider {
    position: absolute;
    left: 44px;
    right: 44px;
    height: 1px;
    background: var(--green);
  }
  .divider--main { top: 176px; }
  .divider--contact { top: 286px; right: 360px; }
  .address {
    position: absolute;
    right: 44px;
    top: 190px;
    margin: 0;
    color: var(--white);
    font-size: 15px;
    font-weight: 500;
    text-align: right;
    line-height: 1.35;
    font-style: normal;
  }
  .person {
    position: absolute;
    left: 44px;
    top: 196px;
  }
  .person__name {
    margin: 0;
    color: var(--green);
    font-weight: 800;
    font-size: 28px;
    letter-spacing: 0.5px;
    text-transform: uppercase;
  }
  .person__title, .person__licence {
    margin: 2px 0 0;
    font-size: 15px;
    font-weight: 500;
  }
  .person__title { color: var(--white); }
  .person__licence { color: var(--green); }
  .contact {
    position: absolute;
    left: 44px;
    top: 304px;
    margin: 0;
    padding: 0;
    list-style: none;
  }
  .contact__item {
    display: flex;
    align-items: center;
    gap: 10px;
    color: var(--white);
    font-size: 15px;
    font-weight: 500;
    margin-bottom: 10px;
  }
  .contact__icon { width: 15px; height: 15px; flex: none; }
</style>
</head>
<body>
<div class="canvas">
  <section class="card card--front" aria-label="Card front">
    <div class="brand">
      <span class="brand__square"></span>
      <h1 class="brand__name">Thornbury<br>Building Company</h1>
    </div>
  </section>

  <section class="card card--back" aria-label="Card back">
    <div class="back-brand">
      <span class="brand__square"></span>
      <p class="back-brand__name">Thornbury<br>Building Company</p>
    </div>

    <div class="divider divider--main"></div>

    <address class="address">487 Larkspur Ln, Wrenfield<br>CA 95033</address>

    <div class="person">
      <h2 class="person__name">Marcus Thornbury</h2>
      <p class="person__title">Project Manager</p>
      <p class="person__licence">Lic# 2468317</p>
    </div>

    <div class="divider divider--contact"></div>

    <ul class="contact">
      <li class="contact__item">
        <svg class="contact__icon" viewBox="0 0 24 24" aria-hidden="true">
          <path fill="#6cb944" d="M6.6 10.8a15.1 15.1 0 0 0 6.6 6.6l2.2-2.2a1 1 0 0 1 1-.25 11.4 11.4 0 0 0 3.6.57 1 1 0 0 1 1 1V20a1 1 0 0 1-1 1A17 17 0 0 1 3 4a1 1 0 0 1 1-1h3.5a1 1 0 0 1 1 1c0 1.25.2 2.45.57 3.57a1 1 0 0 1-.25 1z"/>
        </svg>
        555.274.8136
      </li>
      <li class="contact__item">
        <svg class="contact__icon" viewBox="0 0 24 24" aria-hidden="true">
          <rect x="2" y="5" width="20" height="14" rx="1.5" fill="#6cb944"/>
          <path d="M3 6l9 7 9-7" fill="none" stroke="#1c1c1c" stroke-width="1.8"/>
        </svg>
        thornburybuildingcompany@mailvesta.com
      </li>
    </ul>
  </section>
</div>
</body>
</html>
```